Website Re-design for Kids Playhouse Business

Need current website which looks very outdated to be re-designed to look modern and contemporary, reduce clutter significantly and make it look elegant and simple.
Current website: http://www.tumblenest.com.au/
A website which the business owner likes, use as reference/inspiration: http://vexa.com.au/
Looking for light green palette, natural colours. "WHAT'S ON" page/link no longer required.
Industry/Entity Type
Business
Number of Pages Required
5+ page
Look and feel
Each slider illustrates characteristics of the customer's brand and the style your logo design should communicate.

```html
<!DOCTYPE html>
<html lang="en">
<head>
<meta charset="utf-8">
<title>Tumble Nest – Playhouse &amp; Cafe</title>
<link rel="stylesheet" href="https://fonts.googleapis.com/css2?family=Poppins:ital,wght@0,400;0,500;0,600;0,700;1,600&display=swap">
<style>
:root{
  --green:#76cc52;
  --green-deep:#62b93e;
  --green-ring:#5aae37;
  --green-light:#92e06a;
  --green-footer:#6cc548;
  --white:#ffffff;
  --ink:#3d3d3d;
  --muted:#7a7a7a;
  --red:#e4121b;
  --field:#f4f4f4;
}
*{box-sizing:border-box;margin:0;padding:0}
html,body{width:1200px;height:4225px;overflow:hidden}
body{position:relative;font-family:'Poppins',sans-serif;color:var(--white);background:var(--green)}
.abs{position:absolute}

/* hero */
.hero-photo{left:0;top:0;width:1200px;height:760px;background:linear-gradient(160deg,#d9d2c8 0%,#b9a893 40%,#8f7e6c 75%,#c7bcae 100%)}
.brand{left:168px;top:52px;width:184px;height:88px;background:var(--white);border:3px solid #8b5a2b;border-radius:6px;display:flex;align-items:center;justify-content:center;color:var(--red);font-weight:700;font-size:26px}
.top-btn{top:62px;height:42px;border-radius:21px;font-size:15px;font-weight:500;display:flex;align-items:center;justify-content:center;color:var(--white)}
.btn-eclub{left:542px;width:178px;background:var(--red)}
.btn-call{left:726px;width:180px;background:var(--green)}
.btn-menu{left:924px;width:116px;background:var(--green)}
.btn-menu svg{margin-right:8px}
.slide-arrow{top:340px;width:36px;height:36px;border-radius:50%;border:2px solid rgba(255,255,255,.7)}
.slide-arrow.left{left:34px}.slide-arrow.right{right:34px}
.slide-arrow svg{display:block;margin:8px auto}

.cloud{left:0;width:1200px}

/* welcome */
.welcome{left:0;top:760px;width:1200px;text-align:center}
.welcome h1{font-size:40px;font-weight:600;margin-top:0}
.welcome h2{font-size:27px;font-weight:600;margin-top:4px}
.welcome p{width:740px;margin:18px auto 0;font-size:12.5px;line-height:1.85;opacity:.92}
.outline-btn{display:inline-flex;align-items:center;justify-content:center;height:48px;border:2px solid var(--white);border-radius:24px;font-size:16px;font-weight:500;color:var(--white)}
.welcome .outline-btn{width:164px;margin-top:24px}

.section-title{width:1200px;left:0;text-align:center;font-size:40px;font-weight:600}

/* features */
.feature-pic{width:270px;height:270px;border-radius:50%;border:16px solid var(--green-ring);box-shadow:0 30px 24px -14px rgba(0,0,0,.18)}
.feature-text{width:400px}
.feature-text h3{font-size:26px;font-weight:600;line-height:1.3}
.feature-text p{font-size:12.5px;line-height:1.75;margin-top:10px;opacity:.9}
.feature-text .outline-btn{width:164px;margin-top:22px}

/* testimonial */
.quote-badge{left:570px;top:2488px;width:56px;height:56px;border-radius:50%;border:2px solid var(--white);display:flex;align-items:center;justify-content:center}
.quote{left:250px;top:2566px;width:700px;text-align:center;font-style:italic;font-weight:600;font-size:21px;line-height:1.9}
.quote-author{left:0;top:2684px;width:1200px;text-align:center;font-size:26px;font-weight:600}
.dots{left:572px;top:2748px;display:flex;gap:6px}
.dots span{width:10px;height:10px;border-radius:50%;background:var(--green-deep)}
.dots span.on{background:var(--white)}

/* info columns */
.info-pic{width:236px;height:236px;border-radius:50%;border:14px solid var(--green-ring);box-shadow:0 26px 20px -12px rgba(0,0,0,.15)}
.info-col{width:300px;text-align:center}
.info-col h3{font-size:34px;font-weight:600}
.info-col p{font-size:12px;line-height:1.75;margin:8px auto 0;width:250px;opacity:.92}
.info-col .outline-btn{width:164px;margin-top:20px}

/* contact */
.contact-title{left:0;top:3512px;width:1200px;text-align:center;color:var(--green-deep);font-size:40px;font-weight:600}
.contact-sub{left:0;top:3572px;width:1200px;text-align:center;color:var(--ink);font-size:16px}
.field{height:42px;background:var(--white);border:2px solid #d8d8d8;border-radius:21px;color:var(--ink);font-size:13px;padding:0 20px;display:flex;align-items:center}
.field.message{height:108px;align-items:flex-start;padding-top:12px;border-radius:20px}
.captcha{left:332px;top:3873px;width:254px;height:56px;background:var(--field);border:1px solid #d0d0d0;border-radius:8px;color:var(--muted);font-size:10px;padding:8px 12px}
.captcha .row{display:flex;align-items:center;gap:10px;font-size:14px;color:var(--ink)}
.captcha .tag{margin-left:auto;background:#555;color:var(--white);font-size:8px;padding:2px 6px;border-radius:2px}
.send-btn{left:597px;top:3877px;width:146px;height:44px;border-radius:22px;background:var(--green);color:var(--white);font-size:14px;font-weight:600;display:flex;align-items:center;justify-content:center}

/* footer */
.socials{left:562px;top:4042px;display:flex;gap:10px}
.socials span{width:34px;height:34px;border-radius:50%;background:#4f9a30}
.footer-line{left:0;width:1200px;text-align:center;font-size:14px;font-weight:500}
.footer-line .sep{margin:0 14px}
.footer-small{font-size:12.5px}
.page-num{right:196px;top:4178px;font-size:12px}
</style>
</head>
<body>

<!-- hero -->
<div class="abs hero-photo" role="img" aria-label="Photo of two toddlers playing with soft toys on a playroom floor"></div>
<div class="abs brand">Tumble Nest</div>
<div class="abs top-btn btn-eclub">Join Our E-club</div>
<div class="abs top-btn btn-call">Call: 02 5550 0142</div>
<div class="abs top-btn btn-menu"><svg width="16" height="14" viewBox="0 0 16 14"><rect y="1" width="16" height="2.4" fill="#fff"/><rect y="6" width="16" height="2.4" fill="#fff"/><rect y="11" width="16" height="2.4" fill="#fff"/></svg>Menu</div>
<div class="abs slide-arrow left"><svg width="12" height="16" viewBox="0 0 12 16"><path d="M9 2 3 8l6 6" stroke="#fff" stroke-width="2" fill="none"/></svg></div>
<div class="abs slide-arrow right"><svg width="12" height="16" viewBox="0 0 12 16"><path d="M3 2l6 6-6 6" stroke="#fff" stroke-width="2" fill="none"/></svg></div>

<svg class="abs cloud" style="top:640px" width="1200" height="130" viewBox="0 0 1200 130">
  <g fill="var(--green)">
    <ellipse cx="60" cy="110" rx="160" ry="60"/>
    <ellipse cx="270" cy="105" rx="170" ry="62"/>
    <ellipse cx="470" cy="80" rx="170" ry="70"/>
    <ellipse cx="660" cy="72" rx="180" ry="70"/>
    <ellipse cx="860" cy="90" rx="170" ry="64"/>
    <ellipse cx="1060" cy="100" rx="180" ry="62"/>
    <rect x="0" y="110" width="1200" height="20"/>
  </g>
</svg>

<!-- welcome -->
<section class="abs welcome">
  <h1>Welcome to Tumble Nest</h1>
  <h2>Sydney's newest and best party &amp; play centre!</h2>
  <p>Tumble Nest is an indoor play centre and cafe that offers both kids and adults a chance to enjoy their time together. We pride ourselves on offering the best indoor play space for your little ones to engage in fun and learning activities in a carefully created environment that is not only warm and safe but also sparks creativity and curiosity in every child. Our themed party rooms are hand painted by a muralist and have welcomed thousands of happy children.</p>
  <span class="outline-btn">Read More</span>
</section>

<!-- features -->
<h2 class="abs section-title" style="top:1132px">Our Features</h2>

<div class="abs feature-pic" style="left:231px;top:1234px;background:linear-gradient(135deg,#f0e6f2,#c996c9 60%,#e85a8a)" role="img" aria-label="Photo of children celebrating at a birthday party"></div>
<div class="abs feature-text" style="left:544px;top:1228px">
  <h3>Perfect venue for<br>birthdays and private parties</h3>
  <p>Celebrate in a bright, safe space with games, music and treats prepared by our friendly team, so you can relax while the little ones play for hours.</p>
  <span class="outline-btn">View Parties</span>
</div>

<div class="abs feature-text" style="left:234px;top:1530px">
  <h3>4 kids loving<br>party rooms themes</h3>
  <p>Choose from four hand painted rooms, each with its own story and colours, and let every guest step into a world made just for the birthday child.</p>
  <span class="outline-btn">View Party rooms</span>
</div>
<div class="abs feature-pic" style="left:696px;top:1507px;background:linear-gradient(135deg,#f5f0d8,#c2a06a 55%,#9c4a3a)" role="img" aria-label="Photo of a hand painted fairy tale themed party room"></div>

<div class="abs feature-pic" style="left:231px;top:1817px;background:linear-gradient(135deg,#f4c1d7,#c24c74 55%,#5c3a4a)" role="img" aria-label="Photo of children with a costumed character at a holiday program"></div>
<div class="abs feature-text" style="left:544px;top:1826px">
  <h3>We host school<br>holiday programs</h3>
  <p>During school breaks we run crafts, games and active play sessions guided by caring staff, giving children a full day of fun and parents some time out.</p>
  <span class="outline-btn">View Programs</span>
</div>

<div class="abs feature-text" style="left:234px;top:2128px">
  <h3>Exclusive specials<br>&amp; promotions</h3>
  <p>Look out for weekday deals, cafe combos and seasonal offers that make every visit better value, and join our e-club to hear about them first.</p>
  <span class="outline-btn">View More</span>
</div>
<div class="abs feature-pic" style="left:696px;top:2119px;background:linear-gradient(135deg,#5fa3d8,#1e4f9a 55%,#3db0c8)" role="img" aria-label="Photo of a colourful ball pit in the play area"></div>

<!-- testimonial band -->
<svg class="abs cloud" style="top:2390px" width="1200" height="1080" viewBox="0 0 1200 1080">
  <g fill="var(--green-light)">
    <ellipse cx="80" cy="130" rx="190" ry="70"/>
    <ellipse cx="320" cy="105" rx="190" ry="75"/>
    <ellipse cx="600" cy="80" rx="200" ry="85"/>
    <ellipse cx="880" cy="105" rx="190" ry="75"/>
    <ellipse cx="1120" cy="130" rx="190" ry="70"/>
    <rect x="0" y="130" width="1200" height="950"/>
  </g>
</svg>
<div class="abs quote-badge"><svg width="22" height="16" viewBox="0 0 22 16"><path d="M2 14c0-6 2-10 7-12M13 14c0-6 2-10 7-12" stroke="#fff" stroke-width="2" fill="none"/></svg></div>
<p class="abs quote">Love this place, lots of variety for the kids especially in school holidays !! They'll be entertained for hours whilst you enjoy delicious food or a great coffee !! Highly recommend it !!</p>
<p class="abs quote-author">-Mara Quillon</p>
<div class="abs dots"><span class="on"></span><span></span><span></span><span></span></div>

<!-- info columns -->
<div class="abs info-pic" style="left:164px;top:2806px;background:linear-gradient(135deg,#f2c46a,#b1451f 55%,#4a2a22)" role="img" aria-label="Photo of children at the centre during a visit"></div>
<div class="abs info-col" style="left:132px;top:3068px">
  <h3>Visit Us</h3>
  <p>Find us close to shops and parking, with easy entry for prams and a comfy cafe corner where parents can sit back with a coffee.</p>
  <span class="outline-btn">View Location</span>
</div>

<div class="abs info-pic" style="left:482px;top:2939px;background:linear-gradient(135deg,#cfe3f0,#7c8fb8 55%,#3f4a6a)" role="img" aria-label="Photo of a group of kids with a mascot character"></div>
<div class="abs info-col" style="left:450px;top:3144px">
  <h3>About Us</h3>
  <p>We are a local family business that believes play is the best way to learn, grow and make friends in a safe, happy place.</p>
  <span class="outline-btn">Read More</span>
</div>

<div class="abs info-pic" style="left:798px;top:2806px;background:linear-gradient(135deg,#a7c9e8,#4f8a4a 55%,#7a4f8a)" role="img" aria-label="Painted mural of a colourful landscape"></div>
<div class="abs info-col" style="left:766px;top:3068px">
  <h3>News</h3>
  <p>Read the latest updates on new play equipment, upcoming events, holiday sessions and special days planned at the centre this season.</p>
  <span class="outline-btn">Read More</span>
</div>

<!-- contact -->
<svg class="abs cloud" style="top:3420px" width="1200" height="600" viewBox="0 0 1200 600">
  <g fill="var(--white)">
    <ellipse cx="60" cy="100" rx="200" ry="60"/>
    <ellipse cx="340" cy="78" rx="200" ry="62"/>
    <ellipse cx="600" cy="55" rx="210" ry="70"/>
    <ellipse cx="860" cy="78" rx="200" ry="62"/>
    <ellipse cx="1140" cy="100" rx="200" ry="60"/>
    <rect x="0" y="100" width="1200" height="500"/>
  </g>
</svg>
<h2 class="abs contact-title">Contact Us</h2>
<p class="abs contact-sub">Our postal address and contact details</p>
<div class="abs field" style="left:332px;top:3630px;width:260px">Name*:</div>
<div class="abs field" style="left:608px;top:3630px;width:260px">Phone*:</div>
<div class="abs field" style="left:332px;top:3686px;width:260px">Email*:</div>
<div class="abs field" style="left:608px;top:3686px;width:260px">Postcode*:</div>
<div class="abs field message" style="left:332px;top:3742px;width:536px">Message*:</div>
<div class="abs captcha">
  <div class="row"><svg width="18" height="18" viewBox="0 0 18 18"><path d="M15 9a6 6 0 1 1-2-4.5M15 3v4h-4" stroke="#777" stroke-width="2" fill="none"/></svg>25 + 8 =<span style="width:40px;height:16px;border:1px solid #ccc;background:#fff"></span><span class="tag">CAPTCHA</span></div>
  <div>Enter the answer to avoid spam</div>
</div>
<div class="abs send-btn">SEND MESSAGE</div>

<!-- footer -->
<svg class="abs cloud" style="top:3960px" width="1200" height="265" viewBox="0 0 1200 265">
  <g fill="var(--green-footer)">
    <ellipse cx="90" cy="70" rx="200" ry="50"/>
    <ellipse cx="360" cy="58" rx="200" ry="52"/>
    <ellipse cx="600" cy="40" rx="200" ry="58"/>
    <ellipse cx="840" cy="58" rx="200" ry="52"/>
    <ellipse cx="1110" cy="70" rx="200" ry="50"/>
    <rect x="0" y="70" width="1200" height="195"/>
  </g>
</svg>
<div class="abs socials"><span></span><span></span></div>
<p class="abs footer-line" style="top:4102px">Postal Address: 14 Willow Lane Greenvale 2199 NSW Australia.</p>
<p class="abs footer-line" style="top:4136px">Ph: 02 5550 0142<span class="sep">|</span>Fax: 02 5550 0143<span class="sep">|</span>Email: hello@tumblenest.com.au</p>
<p class="abs footer-line footer-small" style="top:4176px">© 2016 Tumble Nest. All Rights Reserved.<span class="sep">|</span>Terms &amp; Conditions<span class="sep"></span>Privacy Policy</p>
<span class="abs page-num">C4</span>

</body>
</html>
```